Business Card Design

I am an Event and Wedding Planner in need of an eye catching business card featuring my logo (attached), my contact details, and my company tagline (Making every celebration glow with wonder...) I would like the tagline in font similar the logo's font.
Updates
I have just noticed that my logo has a misspelling so for the final design, I will be uploading a corrected logo as soon as I have it.
My apologies.
Reason: Waiting on a corrected logo...Lantern is misspelled and it should say Weddings not Wedding
The logo has been corrected so now Lantern is spelled correctly and it says Weddings instead of Wedding. Please use Edwardian Script ITC as the font for the tagline so it will match the logo. Thank you for your patience.
Target Market(s)
Engaged couples and people hosting milestone celebrations. 25-50 years old, predominately female
Industry/Entity Type
Business
Contact Information for Business Card
Rosalind Merrow, Event Manager / Owner, Mobile: 0491 868 254, Email: rosalind@velvetlanternco.com.au, www.velvetlanternco.com.au, Making every celebration glow with wonder...

```html
<!DOCTYPE html>
<html lang="en">
<head>
<meta charset="utf-8">
<title>Velvet Lantern – Business Card</title>
<link rel="stylesheet" href="https://fonts.googleapis.com/css2?family=Questrial&family=Pinyon+Script&display=swap">
<style>
  :root {
    --backdrop: #e9e6e2;
    --card-light: #ffffff;
    --card-light-edge: #dcdcdc;
    --card-dark: #1e1e1e;
    --card-dark-edge: #2e2e2e;
    --ink: #3a3a3a;
    --ink-strong: #222222;
    --accent: #b3222a;
    --muted: #9a9a9a;
    --paper-text: #f2f2f2;
  }
  * { margin: 0; padding: 0; box-sizing: border-box; }
  html, body {
    width: 1200px; height: 1200px; overflow: hidden;
    background: var(--backdrop);
  }
  .canvas {
    position: relative; width: 1200px; height: 1200px;
    display: flex; flex-direction: column; align-items: center; justify-content: center; gap: 50px;
  }
  .card {
    position: relative; width: 860px; height: 525px;
    box-shadow: 0 10px 30px rgba(0,0,0,.18);
    overflow: hidden;
  }
  .card--front {
    background: radial-gradient(ellipse at 55% 35%, var(--card-light) 40%, var(--card-light-edge) 100%);
    color: var(--ink);
    font-family: "Questrial", "Century Gothic", sans-serif;
  }
  .card--back {
    background: radial-gradient(ellipse at 50% 30%, var(--card-dark-edge) 0%, var(--card-dark) 70%);
    color: var(--paper-text);
    font-family: "Questrial", "Century Gothic", sans-serif;
  }

  /* brand name block */
  .brand {
    position: absolute; display: flex; align-items: center; gap: 16px;
  }
  .brand__name { font-weight: 400; letter-spacing: .02em; white-space: nowrap; }
  .brand__dot { border-radius: 50%; background: var(--accent); flex: none; }

  .card--front .brand { left: 60px; top: 200px; }
  .card--front .brand__name { font-size: 46px; color: var(--ink-strong); }
  .card--front .brand__dot { width: 22px; height: 22px; }

  .card--back .brand { left: 50%; top: 50%; transform: translate(-50%, -50%); }
  .card--back .brand__name { font-size: 78px; color: var(--paper-text); }
  .card--back .brand__dot { width: 34px; height: 34px; }

  /* identity */
  .identity { position: absolute; right: 60px; top: 48px; text-align: right; }
  .identity__name { font-size: 40px; color: var(--ink); }
  .identity__role { font-size: 22px; margin-top: 12px; color: var(--ink); }

  .tagline {
    position: absolute; right: 60px; top: 190px; width: 330px; text-align: center;
    font-family: "Pinyon Script", cursive; font-size: 32px; line-height: 1.4; color: var(--ink-strong);
  }

  /* contacts */
  .contacts { position: absolute; left: 60px; bottom: 48px; list-style: none; }
  .contact { display: flex; align-items: center; gap: 14px; font-size: 24px; color: var(--ink-strong); }
  .contact + .contact { margin-top: 14px; }
  .contact__icon { width: 34px; height: 34px; flex: none; }

  .social { position: absolute; right: 60px; bottom: 140px; display: flex; gap: 10px; }
  .social__dot { width: 34px; height: 34px; border-radius: 50%; background: var(--muted); }
</style>
</head>
<body>
<main class="canvas">

  <section class="card card--front" aria-label="Business card front">
    <div class="brand">
      <span class="brand__name">Velvet Lantern</span>
      <span class="brand__dot"></span>
    </div>

    <header class="identity">
      <h1 class="identity__name" style="font-weight:400">Rosalind Merrow</h1>
      <p class="identity__role">Event Manager / Owner</p>
    </header>

    <p class="tagline">Making every celebration glow with wonder...</p>

    <div class="social" aria-label="Social links">
      <span class="social__dot"></span>
      <span class="social__dot"></span>
    </div>

    <ul class="contacts">
      <li class="contact">
        <svg class="contact__icon" viewBox="0 0 34 34" aria-hidden="true">
          <circle cx="17" cy="17" r="17" fill="#111"/>
          <path d="M12 9c1 0 2 3 2 4s-1.5 1.5-1 2.5c1 2 3 4 5 5 1 .5 1.5-1 2.5-1s4 1 4 2-1.5 3-3 3C15 24 10 19 10 12c0-1.5 1-3 2-3z" fill="#fff"/>
        </svg>
        <span>0491 868 254</span>
      </li>
      <li class="contact">
        <svg class="contact__icon" viewBox="0 0 34 34" aria-hidden="true">
          <circle cx="17" cy="17" r="17" fill="#111"/>
          <rect x="9" y="11" width="16" height="12" fill="none" stroke="#fff" stroke-width="1.8"/>
          <path d="M9 11l8 7 8-7" fill="none" stroke="#fff" stroke-width="1.8"/>
        </svg>
        <span>rosalind@velvetlanternco.com.au</span>
      </li>
      <li class="contact">
        <svg class="contact__icon" viewBox="0 0 34 34" aria-hidden="true">
          <circle cx="17" cy="17" r="17" fill="#111"/>
          <g fill="none" stroke="#fff" stroke-width="1.5">
            <circle cx="17" cy="17" r="8"/>
            <ellipse cx="17" cy="17" rx="3.5" ry="8"/>
            <path d="M9 17h16M10.5 13h13M10.5 21h13"/>
          </g>
        </svg>
        <span>www.velvetlanternco.com.au</span>
      </li>
    </ul>
  </section>

  <section class="card card--back" aria-label="Business card back">
    <div class="brand">
      <span class="brand__name">Velvet Lantern</span>
      <span class="brand__dot"></span>
    </div>
  </section>

</main>
</body>
</html>
```